New, modern business card for growing audiology practice

We need a new business card for our audiology practice. Our logo and website have recently changed (more modern) and we want our business cards to reflect this change.
We conduct hearing tests, perform earwax removals, and fit & dispense hearing aids to our patients. We are a family owned practice in which the owner is the one who works directly with the patient. I have attached logos in various formats to use, as well as two ideas I found on this website; as well as a scanned copy of our current logo. Good luck!

Industry/Entity Type

Business

Contact Information for Business Card

Company name: Tolvera Hearing Center
Provider name: Peter Wolstenby, Au.D. F/NSB
Phone number: (440) 683-5127
Address: 837 W. Lindell Ave. Brannock Falls, OH 44087
email: tolverahearing@postvane.com
website: tolverahearing.com

Colors
000000
aaaaaa
dbdbdb
cacaca
9bcb3c
afd23c
cadf82
b1b1b1

Requirements
Must have
• My card must include information in the "details" section. In the attached images, I found a few that I liked and I would like to model after - "brisky bouncin'" and "Sound Method Center".
• Must be horizontal.
• Must include logos provided. I uploaded them in various file formats and various ways.
• Must match logo font, if possible, if not, please get as close as you can.
Nice to have
• I really like the idea of having a color on one side with just the logo and company name and the contact information and provider name on the other side. I also really like the idea of having the main color dominating on the logo/company side with accent of that same color on the contact side of the card.
Should not have
• Must not be vertical.

```html
<!DOCTYPE html>
<html lang="en">
<head>
<meta charset="utf-8">
<title>Tolvera Hearing Center – Business Card</title>
<link href="https://fonts.googleapis.com/css2?family=Cabin:wght@400&family=Roboto:wght@400;500&family=Roboto+Condensed:wght@700&display=swap" rel="stylesheet">
<style>
  :root {
    --backdrop: #2c2c2c;
    --brand-green: #6f9f36;
    --brand-green-soft: rgba(255,255,255,0.16);
    --card-white: #f2f2f2;
    --ink: #000000;
    --text-grey: #555555;
    --paper-text: #ffffff;
  }
  * { margin: 0; padding: 0; box-sizing: border-box; }
  html, body { width: 1200px; height: 960px; overflow: hidden; background: var(--backdrop); }
  .canvas { position: relative; width: 1200px; height: 960px; }

  .card {
    position: absolute; left: 320px; width: 600px; height: 345px;
    border-radius: 18px; overflow: hidden;
  }

  /* Front side */
  .card--front { top: 100px; background: var(--brand-green); }
  .front-mark {
    position: absolute; left: 150px; top: -20px; width: 300px; height: 300px;
    border-radius: 50%; border: 34px solid var(--brand-green-soft);
  }
  .front-title {
    position: absolute; left: 96px; top: 162px; width: 414px;
    font-family: "Cabin", sans-serif; font-weight: 400; font-size: 30px; letter-spacing: 0.4px;
    color: var(--ink); text-align: center; line-height: 34px;
    border-bottom: 1.5px solid var(--ink); padding-bottom: 1px;
  }
  .front-web {
    position: absolute; left: 96px; top: 201px; width: 414px;
    font-family: "Roboto", sans-serif; font-size: 14px; letter-spacing: 7.4px;
    color: var(--paper-text); text-align: center;
  }

  /* Back side */
  .card--back { top: 493px; height: 342px; background: var(--card-white); }
  .back-brand {
    position: absolute; left: 35px; top: 45px;
    display: flex; align-items: center; gap: 10px;
    font-family: "Cabin", sans-serif; font-weight: 400; font-size: 21px; color: var(--ink);
  }
  .brand-dot { width: 18px; height: 18px; border-radius: 50%; background: var(--brand-green); }
  .back-mark { position: absolute; left: 370px; top: 40px; }

  .provider { position: absolute; left: 35px; top: 152px; }
  .provider-name {
    font-family: "Roboto Condensed", sans-serif; font-weight: 700; font-size: 22px;
    color: var(--brand-green); line-height: 26px;
  }
  .provider-credential {
    font-family: "Roboto", sans-serif; font-weight: 500; font-size: 14px; color: var(--ink);
    margin-top: 2px;
  }
  .address {
    position: absolute; left: 35px; top: 209px;
    font-family: "Roboto", sans-serif; font-size: 14px; line-height: 19px; color: var(--text-grey);
    font-style: normal;
  }
  .contacts { position: absolute; left: 35px; top: 255px; list-style: none; }
  .contacts li {
    display: flex; align-items: center; gap: 9px; height: 19.5px;
    font-family: "Roboto", sans-serif; font-size: 14px; color: var(--text-grey);
  }
  .contacts svg { width: 14px; height: 14px; fill: var(--brand-green); }
</style>
</head>
<body>
<main class="canvas">

  <section class="card card--front" aria-label="Card front">
    <div class="front-mark" aria-hidden="true"></div>
    <h1 class="front-title">TOLVERA HEARING CENTER</h1>
    <p class="front-web">www.tolverahearing.com</p>
  </section>

  <section class="card card--back" aria-label="Card back">
    <div class="back-brand">
      <span class="brand-dot" aria-hidden="true"></span>
      <span>TOLVERA HEARING CENTER</span>
    </div>

    <svg class="back-mark" width="240" height="290" viewBox="0 0 240 290" aria-hidden="true">
      <circle cx="130" cy="145" r="112" fill="none" stroke="var(--brand-green)" stroke-width="28"/>
    </svg>

    <div class="provider">
      <p class="provider-name">PETER WOLSTENBY</p>
      <p class="provider-credential">AU.D. F/NSB</p>
    </div>

    <address class="address">837 W. Lindell Ave.<br>Brannock Falls, OH 44087</address>

    <ul class="contacts">
      <li>
        <svg viewBox="0 0 24 24" aria-hidden="true"><path d="M6.6 10.8a15.1 15.1 0 0 0 6.6 6.6l2.2-2.2c.3-.3.7-.4 1-.2 1.1.4 2.3.6 3.6.6.6 0 1 .4 1 1V20c0 .6-.4 1-1 1A17 17 0 0 1 3 4c0-.6.4-1 1-1h3.5c.6 0 1 .4 1 1 0 1.3.2 2.5.6 3.6.1.3 0 .7-.2 1z"/></svg>
        <span>(440) 683-5127</span>
      </li>
      <li>
        <svg viewBox="0 0 24 24" aria-hidden="true"><path d="M2 5h20v14H2z M3 6.5v1l9 5.5 9-5.5v-1z" fill-rule="evenodd"/></svg>
        <span>tolverahearing@postvane.com</span>
      </li>
      <li>
        <svg viewBox="0 0 24 24" aria-hidden="true"><circle cx="12" cy="12" r="10"/><path d="M2 12h20M12 2c3 3 3 17 0 20M12 2c-3 3-3 17 0 20" stroke="var(--card-white)" stroke-width="1.6" fill="none"/></svg>
        <span>tolverahearing.com</span>
      </li>
    </ul>
  </section>

</main>
</body>
</html>
```